Business Card Design

IT Solutions company.

I need a professional looking design with my company logo if possible.

Logo is located here:
http://www.brunelwavesystems.co.uk/dev/images/logo1.jpg
Feel free to redesign the logo if you think you have any better suggestions.

Our services include, IT Infrastructure/Telephony Maintenance & Hosting Services. Linux and Windows Solutions, App Development.

Out website is currently under development:
http://www.brunelwavesystems.co.uk/dev/

I'm looking for a colourful but professional looking business card.

Industry/Entity Type

Business

Contact Information for Business Card

BW Brunel Wavesystems Ltd
Martin Hollisby
07700958312
www.brunelwavesystems.co.uk
mhollisby@brunelwavesystems.co.uk

```html
<!DOCTYPE html>
<html lang="en">
<head>
<meta charset="utf-8">
<title>Brunel Wavesystems – Business Card</title>
<link rel="stylesheet" href="https://fonts.googleapis.com/css2?family=Oswald:wght@500&family=Roboto:wght@400&display=swap">
<style>
  :root {
    --bg: #e4e2de;
    --card: #ffffff;
    --dark: #333335;
    --blue: #1e4fb4;
    --ink: #2b2b2d;
    --white: #ffffff;
  }
  html, body {
    margin: 0;
    width: 1200px;
    height: 682px;
    overflow: hidden;
    background: var(--bg);
  }
  .card {
    position: absolute;
    left: 80px;
    top: 44px;
    width: 1040px;
    height: 594px;
    background: var(--card);
    box-shadow: 0 6px 24px rgba(0,0,0,.18);
    overflow: hidden;
    font-family: "Roboto", Arial, sans-serif;
    color: var(--ink);
  }
  .top-band {
    position: absolute; left: 0; top: 0;
    width: 100%; height: 34px;
    background: var(--dark);
  }
  .brand-name {
    position: absolute; left: 70px; top: 114px;
    margin: 0;
    font-family: "Oswald", "Arial Narrow", sans-serif;
    font-weight: 500;
    font-size: 44px;
    line-height: 60px;
    letter-spacing: 1px;
    color: var(--dark);
    text-transform: uppercase;
  }
  .name-band {
    position: absolute; left: 60px; top: 244px;
    right: 0; height: 58px;
    background: var(--blue);
    display: flex; align-items: center;
    color: var(--white);
  }
  .name-icon {
    width: 58px; height: 58px;
    background: var(--dark);
    display: flex; align-items: center; justify-content: center;
  }
  .person-name {
    font-family: "Oswald", "Arial Narrow", sans-serif;
    font-weight: 500;
    font-size: 34px;
    letter-spacing: 1px;
    text-transform: uppercase;
    margin-left: 22px;
  }
  .job-title {
    margin-left: auto;
    margin-right: 44px;
    font-size: 22px;
    letter-spacing: 2px;
    text-transform: uppercase;
  }
  .left-accent {
    position: absolute; left: 0; top: 244px;
    width: 20px; height: 58px;
    background: var(--blue);
  }
  .contacts {
    position: absolute; left: 110px; top: 340px;
    display: grid;
    grid-template-columns: 300px auto;
    row-gap: 22px; column-gap: 50px;
    font-size: 21px;
    letter-spacing: .5px;
  }
  .contact { display: flex; align-items: center; gap: 14px; }
  .contact svg { flex: none; }
  .bottom-band {
    position: absolute; left: 0; bottom: 0;
    width: 100%; height: 78px;
    background: var(--dark);
    color: var(--white);
    display: flex; align-items: center;
    padding-left: 70px; gap: 16px;
    box-sizing: border-box;
    font-size: 21px; letter-spacing: 1px;
  }
</style>
</head>
<body>
<main class="card">
  <div class="top-band"></div>

  <h1 class="brand-name">BW Brunel Wavesystems Ltd</h1>

  <div class="left-accent"></div>
  <div class="name-band">
    <div class="name-icon">
      <svg width="30" height="30" viewBox="0 0 24 24" aria-hidden="true">
        <circle cx="12" cy="8" r="5" fill="#fff"/>
        <path d="M2 23c0-6 4.5-9 10-9s10 3 10 9z" fill="#fff"/>
      </svg>
    </div>
    <div class="person-name">Martin Hollisby</div>
    <div class="job-title">General Manager</div>
  </div>

  <div class="contacts">
    <div class="contact">
      <svg width="20" height="20" viewBox="0 0 24 24" aria-hidden="true"><path d="M6.6 10.8a15 15 0 0 0 6.6 6.6l2.2-2.2a1 1 0 0 1 1-.25 11.4 11.4 0 0 0 3.6.57 1 1 0 0 1 1 1V20a1 1 0 0 1-1 1A17 17 0 0 1 3 4a1 1 0 0 1 1-1h3.5a1 1 0 0 1 1 1c0 1.25.2 2.45.57 3.6a1 1 0 0 1-.25 1z" fill="#2b2b2d"/></svg>
      <span>01632 960417</span>
    </div>
    <div class="contact">
      <svg width="22" height="18" viewBox="0 0 24 18" aria-hidden="true"><rect x="1" y="1" width="22" height="16" rx="1" fill="none" stroke="#2b2b2d" stroke-width="2"/><path d="M1 2l11 8 11-8" fill="none" stroke="#2b2b2d" stroke-width="2"/></svg>
      <span>mhollisby@brunelwavesystems.co.uk</span>
    </div>
    <div class="contact">
      <svg width="20" height="22" viewBox="0 0 16 24" aria-hidden="true"><rect x="1.5" y="1" width="13" height="22" rx="2" fill="none" stroke="#2b2b2d" stroke-width="2"/><circle cx="8" cy="19" r="1.3" fill="#2b2b2d"/></svg>
      <span>07700958312</span>
    </div>
    <div class="contact">
      <svg width="22" height="22" viewBox="0 0 24 24" aria-hidden="true"><circle cx="12" cy="12" r="10" fill="none" stroke="#2b2b2d" stroke-width="2"/><ellipse cx="12" cy="12" rx="4.5" ry="10" fill="none" stroke="#2b2b2d" stroke-width="2"/><path d="M2 12h20" stroke="#2b2b2d" stroke-width="2"/></svg>
      <span>www.brunelwavesystems.co.uk</span>
    </div>
  </div>

  <div class="bottom-band">
    <svg width="18" height="26" viewBox="0 0 18 26" aria-hidden="true"><path d="M9 1a8 8 0 0 0-8 8c0 6 8 16 8 16s8-10 8-16a8 8 0 0 0-8-8z" fill="#fff"/><circle cx="9" cy="9" r="3" fill="#333335"/></svg>
    <span>42 Harbour Road, Unit 3, Westbridge</span>
  </div>
</main>
</body>
</html>
```